Flyer needed For the Council for Stewardship in Civic Ventures

With an increasing need for professional staffing in our design and construction industry it is important for organizations to be able to attract, support, and retain people of all genders. With the increase of women entering the design/construction industry, we need to be able to identify and address the specific needs of women in our industry, including those A/E’s who are on the facility Owner side.

This Forum will provide a venue to openly discuss the issues affecting our industry and ideas to address those issues.The program includes time for presentations and a panel discussion by accomplished women in our industry, and facilitated table and open discussions to form solutions with your peers. You will come away with ideas you can implement within your organization to build processes and a supportive culture for women

IN THE ATTACHMENTS
* you'll find our company logo

Target Market(s)

Women in the design and construction industry

Industry/Entity Type

Construction

Requirements
Must have
• Logo, event name, date, time, location, panelists names and pics, PBQ continuing education provided, contact information: Doreen Haskwell, doreen.haskwell@c-scvx.org, (512) 847-3096
• Register at: www.c-scvx.org/events
• Design should encompass the description given above.
Nice to have
• Colors that compliment our logo

```html
<!DOCTYPE html>
<html lang="en">
<head>
<meta charset="utf-8">
<title>AEC Industry Women's Mini-Forum &amp; Workshop</title>
<link rel="stylesheet" href="https://fonts.googleapis.com/css2?family=Oswald:wght@400;500&family=Tinos:wght@400;700&family=Arimo:wght@400;700&display=swap">
<style>
  :root {
    --plum-deep: #2a0f45;
    --plum: #4a2470;
    --plum-glow: #6a3a94;
    --lime: #a6d35a;
    --leaf: #7cc242;
    --white: #ffffff;
    --band-top: #d7dff0;
    --band-bottom: #b9c4e2;
    --ink-purple: #4b2578;
    --photo-a: #8a6aa8;
    --photo-b: #5a3a7c;
  }
  * { margin: 0; padding: 0; box-sizing: border-box; }
  html, body { width: 857px; height: 1200px; overflow: hidden; }
  body { background: var(--plum-deep); }
  .flyer {
    position: relative;
    width: 857px;
    height: 1200px;
    overflow: hidden;
    background: radial-gradient(ellipse 70% 45% at 50% 40%, var(--plum-glow) 0%, var(--plum) 45%, var(--plum-deep) 100%);
    color: var(--white);
    text-align: center;
  }
  .brand { position: absolute; left: 22px; top: 18px; text-align: left; }
  .brand-name {
    display: flex; align-items: center; gap: 12px;
    font-family: 'Oswald', sans-serif; font-weight: 500;
    font-size: 54px; line-height: 1; color: var(--leaf);
  }
  .brand-dot { width: 26px; height: 26px; border-radius: 50%; background: var(--leaf); }
  .brand-full { margin-top: 8px; font-family: 'Arimo', sans-serif; font-size: 13px; color: var(--leaf); }
  .ce-mark {
    position: absolute; right: 0; top: 0;
    width: 140px; height: 130px; background: var(--white);
    display: flex; align-items: center; justify-content: center; gap: 10px;
    font-family: 'Arimo', sans-serif; font-weight: 700; font-size: 34px; color: var(--plum-deep);
  }
  .ce-mark .square { width: 18px; height: 18px; background: var(--plum-deep); }
  .headline { position: absolute; top: 184px; left: 0; right: 0; font-family: 'Oswald', sans-serif; }
  .industry { font-size: 36px; font-weight: 400; color: var(--lime); letter-spacing: 1px; line-height: 1.2; }
  .event-name { font-size: 42px; font-weight: 500; color: var(--lime); line-height: 1.25; }
  .date { font-size: 36px; font-weight: 500; color: var(--white); line-height: 1.3; letter-spacing: 1px; }
  .date .time { font-size: 28px; font-weight: 400; }
  .venue { font-family: 'Tinos', serif; font-size: 23px; line-height: 1.5; }
  .program {
    position: absolute; top: 396px; left: 0; right: 0;
    font-family: 'Tinos', serif; font-size: 17px; line-height: 19.6px;
  }
  .credit {
    position: absolute; top: 738px; left: 0; right: 0;
    font-family: 'Arimo', sans-serif; font-size: 40px; color: var(--lime);
  }
  .contact-band {
    position: absolute; left: 0; right: 0; bottom: 0; height: 392px;
    background: linear-gradient(180deg, var(--band-top), var(--band-bottom));
    color: var(--ink-purple); font-family: 'Arimo', sans-serif;
  }
  .contact-title { margin-top: 24px; font-size: 27px; font-weight: 700; }
  .contact-line { font-size: 19px; line-height: 42px; }
  .contact-title + .contact-line { margin-top: 4px; }
  .panel-title { margin-top: 18px; font-size: 17px; font-weight: 700; letter-spacing: 1px; }
  .panelists { display: flex; justify-content: center; gap: 34px; margin-top: 12px; list-style: none; }
  .panelist { width: 128px; }
  .panelist-photo {
    width: 64px; height: 64px; margin: 0 auto 6px; border-radius: 50%;
    background: radial-gradient(circle at 50% 40%, var(--photo-a), var(--photo-b));
  }
  .panelist-name { font-size: 14px; font-weight: 700; line-height: 18px; }
  .panelist-role { font-size: 13px; line-height: 17px; }
  .register { position: absolute; right: 22px; bottom: 16px; font-size: 25px; font-weight: 700; }
</style>
</head>
<body>
<main class="flyer">
  <header class="brand">
    <div class="brand-name"><span class="brand-dot"></span>C-SCVX</div>
    <div class="brand-full">Council for Stewardship in Civic Ventures</div>
  </header>
  <div class="ce-mark"><span class="square"></span>PBQ</div>

  <section class="headline">
    <h2 class="industry">AEC INDUSTRY</h2>
    <h1 class="event-name">Women's Mini-Forum &amp; Workshop</h1>
    <p class="date">JANUARY 13, 2016 <span class="time">· 8:00 AM – 12:00 PM</span></p>
    <p class="venue">Harborline Suites, San Marcos, Texas</p>
  </section>

  <section class="program">
    <p>The program includes time for presentations<br>
    and a panel discussion by<br>
    accomplished women in our industry,<br>
    and facilitated table and open discussions to form<br>
    solutions with your peers.<br>
    You will come away with ideas you can implement<br>
    within your organization<br>
    to build processes and a supportive culture for women.<br>
    A visual note-taker and separate scribe<br>
    will be utilized to compile ideas and solutions,<br>
    for distribution to participants after the event.<br>
    Presenters and Panelists: architect, engineer,<br>
    contractor, sub/trade, facility Owner<br>
    Table Facilitators: one for each table,<br>
    with tables divided into industry segments:<br>
    architects, engineers, contractors, subs/trades, Owners.</p>
  </section>

  <p class="credit">PBQ continuing education</p>

  <footer class="contact-band">
    <p class="contact-title">Contact : Doreen Haskwell</p>
    <p class="contact-line">doreen.haskwell@c-scvx.org</p>
    <p class="contact-line">(512) 847-3096</p>
    <p class="panel-title">PANELISTS</p>
    <ul class="panelists">
      <li class="panelist"><div class="panelist-photo" role="img" aria-label="Portrait photo of panelist Mara Velloso"></div><p class="panelist-name">Mara Velloso</p><p class="panelist-role">Architect</p></li>
      <li class="panelist"><div class="panelist-photo" role="img" aria-label="Portrait photo of panelist Janet Okorie"></div><p class="panelist-name">Janet Okorie</p><p class="panelist-role">Engineer</p></li>
      <li class="panelist"><div class="panelist-photo" role="img" aria-label="Portrait photo of panelist Lise Dunmore"></div><p class="panelist-name">Lise Dunmore</p><p class="panelist-role">Contractor</p></li>
      <li class="panelist"><div class="panelist-photo" role="img" aria-label="Portrait photo of panelist Priya Castell"></div><p class="panelist-name">Priya Castell</p><p class="panelist-role">Sub/Trade</p></li>
      <li class="panelist"><div class="panelist-photo" role="img" aria-label="Portrait photo of panelist Ruth Ambergate"></div><p class="panelist-name">Ruth Ambergate</p><p class="panelist-role">Facility Owner</p></li>
    </ul>
    <p class="register">Register at: www.c-scvx.org/events</p>
  </footer>
</main>
</body>
</html>
```